Martial Arts Website

Redevelopment of existing martial arts website.

The academy teaches traditional shaolin martial arts, including Shaolin Kung Fu, Wu Shu, Tai Chi, Qigong and Wing Chun and the site needs to reflect the traditional roots (eg, no tacky boxing imagery)

Existing website is www.copperlantern.com.au to get a feel for the desired color scheme (black, green and red). The exact colors can be tweaked though. Please only reuse the logo and font (Karate) - there isnt anything else from the current design that needs to remain.

The current website includes links to a ClipHarbor channel that includes demonstrations of the training conducted to better guide the design.

The new website site map will be:
1. Home
2. Programs - summary page describing each form of training
a. Tiny Otters
b. Kids Kung Fu
c. Youth Kung Fu
d. Adults Kung Fu
e. Wing Chun
f. Tai Chi & Qigong
g. Weaponry Classes
h. 72 Arts of Shaolin Conditioning Program
i. Acrobatics and Wu Shu
j. Fitness Boxing
3. Timetable
4. Coaches - summary page describing all coaches
a. Sifu (Master)
b. Sihing Kit
c. Sihing Sam
d. Sihing Marcus
X. ... up to 10 or so coaches
5. Member Zone
6. Contact Us
Updates

Logo now attached to brief - sorry I only have it in PDF

Just to clarify, I am only expecting a PSD design - no HTML required

Reason: Thanks for the designs, we love a lot of them just require a little extra time to tweak the designs and establish the potential. Thanks for your understanding and efforts.

Target Market(s)

Parents, teenagers, young adults, adults, elderly

Industry/Entity Type

Training

Requirements
Must have
• Chinese kung fu dragon imagery throughout the background
Links to Chatterly and ClipHarbor channel
Promo/icon in the header "Try 2 free classes now"
Home page should include an embedded ClipHarbor video

```html
<!DOCTYPE html>
<html lang="en">
<head>
<meta charset="utf-8">
<title>Copper Lantern Martial Arts Academy</title>
<link rel="stylesheet" href="https://fonts.googleapis.com/css2?family=Roboto+Condensed:wght@400;700&family=Arimo:wght@400;700&display=swap">
<style>
:root{
  --page:#f7f7f7;
  --ink:#333333;
  --muted:#555555;
  --green:#1e7a22;
  --green-bright:#2b9a2f;
  --title-green:#3fae4a;
  --dark:#2a2a2a;
  --dark-2:#444444;
  --panel:#e7e7e7;
  --band:#e4e4e4;
  --rule:#c9c9c9;
  --white:#ffffff;
  --accent-red:#d42a1f;
}
*{box-sizing:border-box;margin:0;padding:0}
html,body{width:989px;height:1200px;overflow:hidden}
body{background:var(--page);font-family:"Arimo",Arial,sans-serif;color:var(--ink);position:relative}
.abs{position:absolute}
.top-rule{left:0;top:0;width:989px;height:6px;background:var(--dark)}
.brand-badge{left:30px;top:18px;width:160px;height:160px;border-radius:50%;background:radial-gradient(circle,#e9e9e9 55%,#cfcfcf 100%);display:flex;align-items:center;justify-content:center}
.brand-badge .inner{width:120px;height:120px;border-radius:50%;background:#111;border:6px solid var(--title-green)}
.site-title{left:190px;top:28px;width:580px;text-align:center;font-family:"Roboto Condensed",sans-serif;font-weight:700;font-size:31px;color:var(--title-green)}
.site-tagline{left:190px;top:72px;width:580px;text-align:center;font-family:"Roboto Condensed",sans-serif;font-size:17px;color:#111}
.figure-art{left:764px;top:19px;width:62px;height:104px;background:linear-gradient(180deg,#f2d6c8,#d8322a 40%,#b81f1a);border-radius:30px 30px 6px 6px}
.social-tab{left:825px;top:6px;width:126px;height:33px;background:var(--dark);border-radius:0 0 4px 4px;display:flex;gap:6px;align-items:center;justify-content:center}
.social-tab span{width:21px;height:21px;border-radius:3px;background:#5a5a5a}
.call-box{left:825px;top:54px;width:126px;height:27px;background:var(--dark);color:var(--white);font-family:"Roboto Condensed",sans-serif;font-size:14px;display:flex;align-items:center;justify-content:center;border-radius:2px}
.main-nav{left:186px;top:125px;width:777px;height:54px;background:linear-gradient(180deg,#3a3a3a,#1e1e1e);border-radius:4px 0 0 0;display:flex;align-items:center}
.main-nav a{color:var(--white);text-decoration:none;font-family:"Roboto Condensed",sans-serif;font-size:16px;padding:0 18px;height:54px;line-height:54px;border-right:1px solid #4a4a4a}
.search{margin-left:auto;margin-right:12px;width:182px;height:27px;background:var(--white);border-radius:2px;display:flex;align-items:center}
.search span{flex:1;font-size:12px;color:#666;padding-left:8px}
.search i{width:27px;height:27px;background:#ddd;display:flex;align-items:center;justify-content:center}
.hero{left:31px;top:198px;width:687px;height:311px;border:3px solid #222;background:linear-gradient(180deg,#2c4a7a 0%,#8a6a8a 45%,#e3a46a 62%,#5a4e4e 78%,#3c3636 100%)}
.hero-copy{position:absolute;left:383px;top:50px;width:290px;color:var(--white)}
.hero-copy h2{font-family:"Roboto Condensed",sans-serif;font-size:19px;font-weight:700;margin-bottom:12px}
.hero-copy p{font-size:11.5px;line-height:17px}
.btn-more{position:absolute;left:385px;top:166px;width:74px;height:31px;background:var(--green);border:1px solid #0f5a12;color:var(--white);font-family:"Roboto Condensed",sans-serif;font-size:14px;display:flex;align-items:center;justify-content:center;border-radius:2px}
.side-panel{left:736px;width:227px;background:var(--panel)}
.panel-head{height:37px;background:linear-gradient(180deg,#3a3a3a,#1c1c1c);color:var(--white);font-family:"Roboto Condensed",sans-serif;font-weight:700;font-size:19px;padding-left:13px;line-height:37px;position:relative}
.class-list{list-style:none;padding:10px 6px 0 13px}
.class-list li{font-size:13.5px;color:#444;height:28px;line-height:28px;border-bottom:1px solid #d4d4d4}
.class-list li:last-child{border-bottom:none}
.class-list li:before{content:"» ";color:#777}
.panel-text{font-family:"Roboto Condensed",sans-serif;font-size:14.5px;padding:10px 14px 0;color:#222}
.signup{display:flex;margin:10px 14px 0;height:26px}
.signup span{flex:1;background:var(--white);border:1px solid #ccc;font-size:12px;line-height:24px;padding-left:7px}
.signup b{width:48px;background:var(--green);color:var(--white);font-weight:400;font-size:12.5px;display:flex;align-items:center;justify-content:center}
.badges{display:flex;justify-content:space-around;align-items:center;padding:18px 10px 0}
.badges i{background:#cfcfcf;border:2px solid #888}
.welcome{left:31px;top:530px;width:680px}
.welcome h1{font-family:"Roboto Condensed",sans-serif;font-weight:700;font-size:19px;color:var(--green);padding-bottom:6px;border-bottom:3px dashed #b5b5b5;width:510px;margin-bottom:10px}
.program{font-size:11.5px;line-height:16.5px;color:#333;margin-bottom:10px}
.program strong{color:var(--green);font-size:13px}
.program em{font-style:normal;font-weight:700;color:#222}
.band{left:0;top:867px;width:989px;height:266px;background:var(--band)}
.col-title{font-family:"Roboto Condensed",sans-serif;font-weight:700;font-size:16px;color:#444;padding-bottom:3px;border-bottom:3px dashed #a9a9a9;width:56px;white-space:nowrap}
.feed{width:238px}
.feed-item{padding:10px 0 8px;border-bottom:1px solid #bdbdbd;font-size:11.5px;line-height:17px;color:#555}
.feed-item:last-child{border-bottom:none}
.feed-item b{display:block;color:#333}
.calendar{left:736px;top:918px;width:227px;border:2px solid #777;background:#cfcfcf}
.cal-head{height:36px;background:linear-gradient(180deg,#3a3a3a,#1c1c1c);color:var(--white);font-family:"Roboto Condensed",sans-serif;font-size:17px;display:flex;align-items:center;justify-content:space-between;padding:0 6px}
.cal-head i{width:22px;height:22px;border-radius:4px;background:#555;display:flex;align-items:center;justify-content:center;font-style:normal;font-size:10px}
.cal-table{width:100%;border-collapse:collapse;font-family:"Roboto Condensed",sans-serif;font-size:15px;text-align:center}
.cal-table th{height:23px;font-weight:700;color:#222;background:#d9d9d9}
.cal-table td{height:25.5px;border:1px solid #bdbdbd;background:#e6e6e6;color:#222}
.cal-table td.other{color:#888}
.cal-table td.today{background:var(--green);color:var(--white)}
.footer-links{left:0;top:1150px;width:989px;text-align:center;font-size:11.5px;color:#555}
.footer-copy{left:0;top:1168px;width:989px;text-align:center;font-size:11.5px;color:#555}
</style>
</head>
<body>
<div class="abs top-rule"></div>

<div class="abs brand-badge"><div class="inner" role="img" aria-label="Academy emblem"></div></div>
<div class="abs site-title">Copper Lantern Martial Arts Academy</div>
<div class="abs site-tagline">Traditional Kung Fu &amp; Tai Chi Training Center</div>
<div class="abs figure-art" role="img" aria-label="Martial artist in red uniform in a fighting stance"></div>

<div class="abs social-tab"><span></span><span></span><span></span><span></span></div>
<div class="abs call-box">Call: (02) 4810 5530</div>

<nav class="abs main-nav">
  <a href="#">Home</a><a href="#">Programs</a><a href="#">Timetable</a><a href="#">Coaches</a><a href="#">Member Zone</a><a href="#" style="border-right:none">Contact Us</a>
  <div class="search"><span>Search...</span><i><svg width="12" height="12" viewBox="0 0 12 12"><circle cx="5" cy="5" r="3.5" fill="none" stroke="#333" stroke-width="1.6"/><line x1="7.5" y1="7.5" x2="11" y2="11" stroke="#333" stroke-width="1.8"/></svg></i></div>
</nav>

<section class="abs hero" role="img" aria-label="Martial artists training on a beach at sunset">
  <div class="hero-copy">
    <h2>Copper Lantern Martial Arts Academy</h2>
    <p>Copper Lantern Martial Arts Academy is a purpose built (design and fitted), traditional martial arts centre providing professional, quality instruction in martial arts for all ages and physical capabilities.</p>
  </div>
  <div class="btn-more">More Info</div>
</section>

<aside class="abs side-panel" style="top:198px;height:311px">
  <div class="panel-head">Classes</div>
  <ul class="class-list">
    <li>Tiny Otters</li><li>Kids Kung Fu</li><li>Youth Kung Fu</li><li>Adults Kung Fu</li><li>Wing Chun</li><li>Tai Chi &amp; Qigong</li><li>Weaponry Classes</li><li>72 Arts of Shaolin</li><li>Performance Team</li>
  </ul>
</aside>

<aside class="abs side-panel" style="top:527px;height:114px">
  <div class="panel-head">Newsletter
    <svg style="position:absolute;right:10px;top:7px" width="36" height="24" viewBox="0 0 36 24"><rect x="1" y="1" width="34" height="22" fill="#fff" stroke="#fff"/><polyline points="1,1 18,13 35,1" fill="none" stroke="#222" stroke-width="1.5"/></svg>
  </div>
  <p class="panel-text">Lorem Ipsum is simply dummy text</p>
  <div class="signup"><span>Enter Your Email</span><b>Submit</b></div>
</aside>

<aside class="abs side-panel" style="top:656px;height:149px">
  <div class="panel-head">Accreditation</div>
  <p class="panel-text">Lorem Ipsum is simply dummy text</p>
  <div class="badges">
    <i style="width:56px;height:36px;border-radius:50%"></i>
    <i style="width:38px;height:38px;border-radius:4px"></i>
    <i style="width:56px;height:56px;border-radius:50%"></i>
  </div>
</aside>

<section class="abs welcome">
  <h1>Welcome to Copper Lantern Martial Arts Academy - NSW Australia</h1>
  <p class="program"><strong>Tiny Otters – </strong><em>ages 4 to 6</em>. A specialised martial arts program for ages 4 to 6.</p>
  <p class="program"><strong>Kids Kung Fu – </strong> <em>ages 6 to 11</em>. Practical, Responsible Instruction. Plus, we specialize in powerful character development skills in a positive environment. Kids learn self defence NOT fighting, anti bullying techniques.</p>
  <p class="program"><strong>Youth Kung Fu – </strong> <em>ages 11 to 15</em>. The ultimate way to Build Confidence, Self-Esteem, Self-Discipline, and Athletic Skills, while learning self defence in a tradition style Martial Arts.</p>
  <p class="program"><strong>Adults Shaolin Kung Fu – </strong> <em>ages 15 &amp; over</em>. Self defence utilizing great range of punches, kicks, joint-locking, throwing and grappling techniques. The class utilizes traditional training methods designed to develop a sound mind and body.</p>
  <p class="program"><strong>Wing Chun Kung Fu – </strong> <em>ages 13 &amp; over</em>. Authentic Wing Chun Kung Fu by Crane Ridge Wing Chun in the direct lineage to Tam Kwok (World famous Wing Chun Master). Effective, direct, efficient Self Defence.</p>
  <p class="program"><strong>Tai Chi &amp; Qigong</strong>&nbsp; Classes suitable for all ages and physical capabilities "The art of self healing and preservation"</p>
  <p class="program"><strong>Weaponry</strong>&nbsp; Learn Traditional Kung Fu weapons, Wu Shu weapons &amp; Tai Chi weapons.</p>
  <p class="program"><strong>72 Arts Of Shaolin</strong>&nbsp; Conditioning program using training methods of Ancient Shaolin warriors.</p>
</section>

<div class="abs band"></div>

<section class="abs feed" style="left:31px;top:882px">
  <h3 class="col-title">News</h3>
  <div class="feed-item"><b>17 September, 2012</b>See the "Timetable" page for new timetable and classes. Copper Lantern Hosts: "A day with the masters".</div>
  <div class="feed-item"><b>17 September, 2012</b>Grand Master Lo Wen Hai to visit our Kwoon. The Copper Lantern monthly news letter now avaialble online. 2011</div>
  <div class="feed-item"><b>17 September, 2012</b>Grand Master Lo Wen Hai to visit our Kwoon. The Copper Lantern monthly news letter now avaialble online. 2011</div>
</section>

<section class="abs feed" style="left:371px;top:882px;width:330px">
  <h3 class="col-title">Blog</h3>
  <div class="feed-item" style="width:237px;width:auto;border-bottom:none;padding-bottom:0">
    <b>17 September, 2012</b>See the "Timetable" page for new timetable and classes. Copper Lantern Hosts: "A day with the masters".
  </div>
  <div style="width:237px;border-bottom:1px solid #bdbdbd;height:8px"></div>
  <div class="feed-item" style="border-bottom:none;padding-bottom:0"><b>17 September, 2012</b>Grand Master Lo Wen Hai to visit our Kwoon. The Copper Lantern monthly news letter now avaialble online. 2011 Copper Lantern</div>
  <div style="width:237px;border-bottom:1px solid #bdbdbd;height:8px"></div>
  <div class="feed-item"><b>17 September, 2012</b>Grand Master Lo Wen Hai to visit our Kwoon. The Copper Lantern monthly news letter now avaialble online. 2011 Copper Lantern</div>
</section>

<h3 class="abs col-title" style="left:736px;top:882px;width:82px">Calendar</h3>
<section class="abs calendar">
  <div class="cal-head"><i>◀</i><span>September 2012</span><i>▶</i></div>
  <table class="cal-table">
    <tr><th>Su</th><th>Mo</th><th>Tu</th><th>We</th><th>Th</th><th>Fr</th><th>Sa</th></tr>
    <tr><td class="other">27</td><td class="other">28</td><td class="other">29</td><td class="other">30</td><td>1</td><td>2</td><td>3</td></tr>
    <tr><td>4</td><td style="background:linear-gradient(225deg,var(--green) 18%,#e6e6e6 18%)">5</td><td>6</td><td>7</td><td>8</td><td>9</td><td>10</td></tr>
    <tr><td>11</td><td>12</td><td>13</td><td>14</td><td>15</td><td>16</td><td class="today">17</td></tr>
    <tr><td>18</td><td>19</td><td>20</td><td style="background:linear-gradient(225deg,var(--accent-red) 18%,#e6e6e6 18%)">21</td><td>22</td><td>23</td><td>24</td></tr>
    <tr><td>25</td><td>26</td><td>27</td><td>28</td><td>29</td><td>30</td><td>31</td></tr>
  </table>
</section>

<p class="abs footer-links">Home &nbsp;|&nbsp; About Us &nbsp;|&nbsp; Timetable &nbsp;|&nbsp; Instructors &nbsp;|&nbsp; Contact Us &nbsp;|&nbsp; Members Zone</p>
<p class="abs footer-copy">Copyright © 2012 - Copper Lantern Martial Arts Pty Ltd. Kingsford Vale NSW 2790</p>
</body>
</html>
```